Business Card Design - Photographer

I am a landscape photographer and I require a business card design. 

I require two designs:
1)  a double sided business card
 and
b)  a single sided business card 

The single sided design can either be the same as the double sided (with just one side having all the information)....or it can be an entire new design. Its up to you.

My corporate colours are (CMYK):

Blue   69, 32, 0, 0
Grey  72,  64,  47,  31
Green  32,  2,  91,  0
Yellow   0, 19, 92, 0
Orange  0, 39, 75, 0

Colour space in final file should be in CMYK.

The details that need to be included on the card:

- Use the provided Logo
- Name: Wiktor Baranowski
- Email:   sales@vistalumeworks.com.au
- Website:    vistalumeworks.com.au
- Twitter:    twitter.com/vistalumeworks
- Facebook:   facebook.com/vistalumeworks
- Mobile  0417 539 662

Please use the attached template to design the logo to the specified size, including the marked bleed lines. I have also attached my logo in PNG (transparent background) and ai format for you to use.

The final file should be:
- Photoshop version with layers so I can edit the name/text etc. All non vector files should be high resolution at 1039 x 697 pixels at 300 dpi.

I also require a file as:
- Vector based PDF

Anyway questions please contact me.

Thank you

Industry/Entity Type

Landscape

Logo styles of interest
Pictorial/Combination Logo
Abstract Logo
Wordmark Logo
Lettermark Logo
Requirements
Must have
• The details that need to be included on the card:

- Use the provided Logo
- Name: Wiktor Baranowski
- Email: sales@vistalumeworks.com.au
- Website: vistalumeworks.com.au
- Twitter: twitter.com/vistalumeworks
- Facebook: facebook.com/vistalumeworks
- Mobile 0417 539 662

```html
<!DOCTYPE html>
<html lang="en">
<head>
<meta charset="utf-8">
<title>Vistalume Works – Business Card</title>
<link rel="stylesheet" href="https://fonts.googleapis.com/css2?family=Cinzel:wght@400;500&family=Open+Sans:wght@400;700&display=swap">
<style>
  :root {
    --stage: #ad8a2c;
    --paper: #ffffff;
    --ink: #3b3f4c;
    --slate: #2b2f3b;
    --slate-light: #3a3f4d;
    --blue: #3d8fd0;
    --green: #a6c944;
    --yellow: #f8c91c;
    --orange: #f7a23c;
    --text: #2a2a2a;
  }
  * { box-sizing: border-box; margin: 0; padding: 0; }
  html, body { width: 1200px; height: 686px; overflow: hidden; }
  body { background: var(--stage); position: relative; font-family: "Open Sans", Arial, sans-serif; }

  .card { position: absolute; width: 525px; height: 300px; box-shadow: 1px 2px 3px rgba(0,0,0,.35); overflow: hidden; }
  .card--front { left: 63px; top: 128px; background: var(--paper); }
  .card--back { left: 612px; top: 289px; width: 523px; height: 299px;
    background: radial-gradient(circle at 25% 20%, var(--slate-light), var(--slate) 70%); }

  .accent { position: absolute; }
  .accent--corner-dark { left: 460px; top: 0; width: 65px; height: 21px; background: var(--slate); }
  .accent--top-band { left: 179px; top: 0; width: 321px; height: 9px;
    background: linear-gradient(90deg, var(--orange), var(--yellow) 35%, var(--green) 65%, var(--blue)); }
  .accent--side-dark { left: 0; top: 239px; width: 21px; height: 61px; background: var(--slate); }
  .accent--side-band { left: 0; top: 215px; width: 10px; height: 67px;
    background: linear-gradient(180deg, var(--orange), var(--yellow) 35%, var(--green) 65%, var(--blue)); }

  .brand { position: absolute; left: 59px; top: 50px; width: 200px; text-align: center; color: var(--ink); }
  .brand__mark { width: 64px; height: 64px; border-radius: 50%; background: var(--ink); margin: 0 auto 10px; }
  .brand__name { font-family: "Cinzel", Georgia, serif; font-size: 20px; font-weight: 500; letter-spacing: .5px;
    white-space: nowrap; padding-bottom: 2px; border-bottom: 1px solid var(--ink); }
  .brand__tagline { font-family: "Cinzel", Georgia, serif; font-size: 8px; letter-spacing: 1.6px; margin-top: 4px; }

  .contact { position: absolute; right: 45px; top: 118px; text-align: right; color: var(--text); font-size: 12px; line-height: 1.3; }
  .contact__address { margin-bottom: 10px; }
  .contact__line { display: flex; justify-content: flex-end; align-items: center; gap: 4px; height: 20px; }
  .contact__line--social { margin-top: 0; height: 20px; font-size: 11.5px; }
  .contact__gap { height: 8px; }
  .icon { width: 11px; height: 11px; flex: none; }
  .icon--square { width: 13px; height: 13px; border-radius: 2px; }
  .icon--square.is-blue { background: #5aafe0; }
  .icon--square.is-navy { background: #3b5a98; }

  .back__mark { position: absolute; left: 172px; top: 46px; width: 164px; height: 164px; border-radius: 50%; background: var(--paper); }
  .back__web { position: absolute; left: 0; right: 0; top: 248px; text-align: center; color: var(--paper);
    font-size: 13px; font-weight: 700; letter-spacing: .2px; }
</style>
</head>
<body>
  <section class="card card--front" aria-label="Business card front">
    <div class="accent accent--corner-dark"></div>
    <div class="accent accent--top-band"></div>
    <div class="accent accent--side-band"></div>
    <div class="accent accent--side-dark"></div>

    <div class="brand">
      <div class="brand__mark"></div>
      <div class="brand__name">VISTALUME WORKS</div>
      <div class="brand__tagline">FINE ART PHOTOGRAPHY</div>
    </div>

    <div class="contact">
      <div class="contact__address">Street name City<br>State, zip code</div>
      <div class="contact__line">
        <svg class="icon" viewBox="0 0 12 12"><path d="M3 1l2 2.5-1 1.2c.6 1.3 1.6 2.3 2.9 2.9l1.2-1L10.6 8.6 9.2 10.8C5 10.3 1.7 7 1.2 2.8z" fill="#3d8fd0"/></svg>
        <span>0417 539 662</span>
      </div>
      <div class="contact__line">
        <svg class="icon" viewBox="0 0 12 12"><rect x="0.5" y="2.5" width="11" height="7.5" fill="#3d8fd0"/><path d="M0.5 2.5L6 7l5.5-4.5" fill="none" stroke="#fff" stroke-width="1"/></svg>
        <span>sales@vistalumeworks.com.au</span>
      </div>
      <div class="contact__line">
        <svg class="icon" viewBox="0 0 12 12"><circle cx="6" cy="6" r="5.3" fill="none" stroke="#3d8fd0" stroke-width="1.2"/><path d="M0.8 6h10.4M6 0.8c-2.4 2.8-2.4 7.6 0 10.4M6 0.8c2.4 2.8 2.4 7.6 0 10.4" fill="none" stroke="#3d8fd0" stroke-width="0.9"/></svg>
        <span>www.vistalumeworks.com.au</span>
      </div>
      <div class="contact__gap"></div>
      <div class="contact__line contact__line--social"><span class="icon icon--square is-blue"></span><span>@vistalumeworks</span></div>
      <div class="contact__line contact__line--social"><span class="icon icon--square is-navy"></span><span>@vistalumeworks</span></div>
    </div>
  </section>

  <section class="card card--back" aria-label="Business card back">
    <div class="back__mark"></div>
    <div class="back__web">www.vistalumeworks.com.au</div>
  </section>
</body>
</html>
```